Bubble map/flip book

I need someone to create a bubble map with explanations using the attached. This will be used to create a color coded flip book/manual. I need you to clean this up.

Marlowesintary@quillpost.net

```html
<!DOCTYPE html>
<html lang="en">
<head>
<meta charset="utf-8">
<title>Claim Has Been Denied</title>
<link rel="stylesheet" href="https://fonts.googleapis.com/css2?family=Arimo:wght@400;700&family=Open+Sans:ital,wght@1,400&display=swap">
<style>
  :root {
    --slate: #48646f;
    --sage: #cfdcd3;
    --teal: #7ba3a1;
    --white: #ffffff;
    --tab: #9aa8a4;
    --auth: #3f5f86;
    --duplicate: #6b4f6e;
    --global: #2f6b66;
    --timely: #8a4f3d;
    --coding: #5f6b3a;
    --noncovered: #7a5a2f;
    --info: #48646f;
  }
  * { margin: 0; padding: 0; box-sizing: border-box; }
  html, body { width: 927px; height: 1200px; overflow: hidden; }
  body { background: var(--sage); font-family: "Arimo", Arial, sans-serif; }
  .page { position: relative; width: 927px; height: 1200px; overflow: hidden; background: var(--sage); }
  .top-band { position: absolute; left: 0; top: 0; width: 927px; height: 328px; background: var(--slate); }
  .title-box {
    position: absolute; left: 84px; top: 254px; width: 758px; height: 146px;
    background: var(--teal); border: 5px solid var(--sage); border-radius: 16px;
    box-shadow: 4px 6px 10px rgba(0,0,0,0.3);
    display: flex; align-items: center; justify-content: center; z-index: 2;
  }
  .title-box h1 {
    color: var(--white); font-weight: 700; font-size: 58px; letter-spacing: 0.5px;
    text-shadow: 3px 4px 6px rgba(0,0,0,0.35); white-space: nowrap;
  }
  .connectors { position: absolute; left: 0; top: 0; z-index: 1; }
  .reason {
    position: absolute; width: 138px; height: 138px;
    border-radius: 6px; color: var(--white);
    display: flex; flex-direction: column; align-items: center; justify-content: center;
    text-align: center; padding: 8px 9px; z-index: 2;
  }
  .reason-label { font-weight: 700; font-size: 18px; line-height: 20px; }
  .reason-label.small { font-size: 15px; line-height: 18px; }
  .reason-note { font-weight: 400; font-size: 11px; line-height: 13px; margin-top: 7px; opacity: 0.92; }
  .row-top { top: 547px; }
  .row-bottom { top: 778px; }
  .auth { left: 87px; background: var(--auth); }
  .duplicate { left: 292px; background: var(--duplicate); }
  .global { left: 498px; background: var(--global); }
  .timely { left: 702px; background: var(--timely); }
  .coding { left: 190px; background: var(--coding); }
  .noncovered { left: 395px; background: var(--noncovered); }
  .info { left: 600px; background: var(--info); }
  .footer-url {
    position: absolute; right: 55px; top: 1142px; font-family: "Open Sans", sans-serif;
    font-style: italic; font-size: 15px; color: var(--slate);
  }
  .page-number {
    position: absolute; left: 894px; top: 1138px; width: 33px; height: 32px;
    background: var(--tab); color: #c9d3cf; font-family: "Open Sans", sans-serif;
    font-size: 22px; display: flex; align-items: center; justify-content: center;
  }
</style>
</head>
<body>
<div class="page">
  <div class="top-band"></div>

  <svg class="connectors" width="927" height="1200" aria-hidden="true">
    <g stroke="#48646f" stroke-width="3">
      <line x1="155" y1="395" x2="155" y2="548"/>
      <line x1="258" y1="395" x2="258" y2="779"/>
      <line x1="361" y1="395" x2="361" y2="548"/>
      <line x1="463" y1="395" x2="463" y2="779"/>
      <line x1="566" y1="395" x2="566" y2="548"/>
      <line x1="669" y1="395" x2="669" y2="779"/>
      <line x1="771" y1="395" x2="771" y2="548"/>
    </g>
  </svg>

  <div class="title-box"><h1>Claim Has Been Denied</h1></div>

  <div class="reason row-top auth">
    <div class="reason-label">Auth /<br>Referral<br>Needed</div>
    <div class="reason-note">Get prior auth or referral, then resubmit.</div>
  </div>
  <div class="reason row-top duplicate">
    <div class="reason-label">Duplicate</div>
    <div class="reason-note">Already on file; check status before refiling.</div>
  </div>
  <div class="reason row-top global">
    <div class="reason-label">Global<br>Inclusive</div>
    <div class="reason-note">Bundled in a global fee; review modifiers.</div>
  </div>
  <div class="reason row-top timely">
    <div class="reason-label">Past<br>Timely<br>Filing</div>
    <div class="reason-note">Sent after deadline; send proof of filing.</div>
  </div>

  <div class="reason row-bottom coding">
    <div class="reason-label">Coding /<br>Billing<br>Issues</div>
    <div class="reason-note">Fix codes or billing data and correct claim.</div>
  </div>
  <div class="reason row-bottom noncovered">
    <div class="reason-label">Non-<br>Covered<br>Charge</div>
    <div class="reason-note">Excluded by the plan; bill the patient.</div>
  </div>
  <div class="reason row-bottom info">
    <div class="reason-label small">Additional<br>Information<br>Requested</div>
    <div class="reason-note">Send the records or details the payer asks for.</div>
  </div>

  <div class="footer-url">www.claimguidepress.com</div>
  <div class="page-number">1</div>
</div>
</body>
</html>
```